Brightwave Reach - Business Card

We need a business card for a Social Media Marketing company that specializes in online marketing for small businesses in Canada using common Social Media platforms such as Pixlora, Chatterly, Blinkpost & Quibber.

I have uploaded a copy of our logo which I would like utilized in the business card. We would like the business card to be modern yet classy design.

Our website is www.brightwavereach.ca

Industry/Entity Type

Marketing

Contact Information for Business Card

Email: info@brightwavereach.ca
Website: www.brightwavereach.ca
Telephone: 604-555-0193

Colors

Designer to choose colors to be used in the design.

Requirements
Must have
• Social Media icons on reverse
• Please add some designs with color.

```html
<!DOCTYPE html>
<html lang="en">
<head>
<meta charset="utf-8">
<title>Brightwave Reach – Business Card</title>
<link href="https://fonts.googleapis.com/css2?family=Lato:wght@400;700;900&display=swap" rel="stylesheet">
<style>
  :root{
    --charcoal:#3d4043;
    --red:#c8202a;
    --white:#ffffff;
    --backdrop:#e4e4e6;
    --ink-soft:#e9e9e9;
  }
  *{margin:0;padding:0;box-sizing:border-box}
  html,body{width:1200px;height:900px;overflow:hidden}
  body{background:var(--backdrop);font-family:'Lato',sans-serif;position:relative}

  .card{position:absolute;left:250px;width:700px;height:400px;border-radius:4px;overflow:hidden;box-shadow:0 6px 18px rgba(0,0,0,.18)}
  .card--back{top:30px;background:var(--charcoal)}
  .card--front{top:470px;background:var(--white)}

  .brand{position:absolute;display:flex;align-items:center;gap:14px;font-weight:900;font-size:34px;letter-spacing:1px;text-transform:uppercase;line-height:1}
  .brand__square{width:26px;height:26px;border:4px solid currentColor}
  .card--front .brand{left:56px;top:70px;color:var(--charcoal)}
  .card--back .brand{left:0;right:0;top:95px;justify-content:center;color:var(--white)}

  .socials{position:absolute;left:0;right:0;top:215px;display:flex;justify-content:center;gap:70px;list-style:none}
  .socials__item{display:flex;flex-direction:column;align-items:center;gap:10px;color:var(--ink-soft);font-size:13px;letter-spacing:.5px}
  .socials__badge{width:46px;height:46px;border-radius:8px;background:var(--red);border:3px solid var(--white)}

  .swoosh{position:absolute;inset:0;width:700px;height:400px}

  .contact{position:absolute;right:34px;bottom:22px;text-align:right;color:var(--white)}
  .contact__name{color:var(--red);font-size:26px;font-weight:400;letter-spacing:.5px;line-height:1.1}
  .contact__title{font-size:16px;line-height:1.3;margin-bottom:8px;color:var(--ink-soft)}
  .contact__line{display:flex;justify-content:flex-end;align-items:center;gap:12px;font-size:16px;line-height:1.4}
  .contact__icon{width:15px;height:15px;flex:none}
</style>
</head>
<body>

<section class="card card--back" aria-label="Card reverse">
  <div class="brand"><span class="brand__square"></span>Brightwave Reach</div>
  <ul class="socials">
    <li class="socials__item"><span class="socials__badge"></span>Chatterly</li>
    <li class="socials__item"><span class="socials__badge"></span>Pixlora</li>
    <li class="socials__item"><span class="socials__badge"></span>Quibber</li>
    <li class="socials__item"><span class="socials__badge"></span>Blinkpost</li>
  </ul>
</section>

<section class="card card--front" aria-label="Card front">
  <svg class="swoosh" viewBox="0 0 700 400" aria-hidden="true">
    <path d="M0,195 C200,290 480,262 700,112 L700,400 L0,400 Z" fill="var(--red)"/>
    <path d="M0,195 C200,290 480,270 700,130 L700,400 L0,400 Z" fill="var(--charcoal)"/>
  </svg>

  <div class="brand"><span class="brand__square"></span>Brightwave Reach</div>

  <div class="contact">
    <p class="contact__name">Daniel Okafor</p>
    <p class="contact__title">Manager</p>
    <p class="contact__line">604-555-0193
      <svg class="contact__icon" viewBox="0 0 16 16" aria-hidden="true"><path d="M3.5 1.5l2.5 0 1 3.5-1.8 1.3a8 8 0 0 0 4.5 4.5L11 9l3.5 1v2.5c0 1-1 2-2 2C6.5 14.5 1.5 9.5 1.5 3.5c0-1 1-2 2-2z" fill="var(--red)"/></svg>
    </p>
    <p class="contact__line">info@brightwavereach.ca
      <svg class="contact__icon" viewBox="0 0 16 16" aria-hidden="true"><rect x="1" y="3" width="14" height="10" rx="1" fill="var(--red)"/><path d="M1.5 4l6.5 5 6.5-5" stroke="var(--charcoal)" stroke-width="1.4" fill="none"/></svg>
    </p>
    <p class="contact__line">www.brightwavereach.ca
      <svg class="contact__icon" viewBox="0 0 16 16" aria-hidden="true"><circle cx="8" cy="8" r="7" fill="var(--red)"/><g stroke="var(--charcoal)" stroke-width="1" fill="none"><ellipse cx="8" cy="8" rx="3" ry="7"/><path d="M1 8h14M2.5 4.5h11M2.5 11.5h11"/></g></svg>
    </p>
  </div>
</section>

</body>
</html>
```